Business card design Needed for new logo / Construction business, home extensions and new builds

We need a business card design using our new logo files which i will attach to this project :)

We are a small construction business specialising in home extensions, new builds and property development. We are very ambitious and would appreciate professional and elegant designs for our new business card.

Very serious about using the services on MakerQuarry and recently acquired our new logo from here :)

Please get involved, i will feedback when i can as i am very busy but can respond daily, thanks

Target Market(s)

People that want to build onto their houses, new building developments or adding too their existing property

Industry/Entity Type

Construction

Contact Information for Business Card

Renwick Tolliver Construction, Lionel Ashby (Managing Director), Tel 07822254961, email - info@renwick-tolliver, www.renwick-tolliver.co.uk

Colors

Designer to choose colors to be used in the design.

Requirements
Must have
• I like a deep grey on the back please. A lot of you have provided black from and back, try mixing things up a little. The black looks cool 😎 Thanks

```html
<!DOCTYPE html>
<html lang="en">
<head>
<meta charset="utf-8">
<title>Renwick Tolliver Construction – Business Card</title>
<link href="https://fonts.googleapis.com/css2?family=Open+Sans:wght@400;600;700&display=swap" rel="stylesheet">
<style>
  :root {
    --stage: #ececec;
    --card-back: #1d1d22;
    --card-back-mark: #2a2a31;
    --card-front: #ffffff;
    --gold: #e3a71f;
    --gold-deep: #c08a2a;
    --gold-soft: #f5ecdc;
    --ink: #1a1a1a;
    --silver: #8d9196;
    --back-text: #e8e8e8;
  }
  * { box-sizing: border-box; margin: 0; padding: 0; }
  html, body { width: 1200px; height: 780px; overflow: hidden; }
  body {
    background: var(--stage);
    font-family: "Open Sans", Arial, sans-serif;
    position: relative;
  }
  .card {
    position: absolute;
    top: 240px;
    width: 525px;
    height: 300px;
    border-radius: 22px;
    overflow: hidden;
    box-shadow: 0 4px 0 var(--gold);
  }
  /* Back */
  .card--back { left: 40px; background: var(--card-back); }
  .back__mark {
    position: absolute;
    left: 0; right: 0; top: 96px;
    text-align: center;
    font-weight: 700;
    font-size: 34px;
    letter-spacing: 3px;
    color: var(--card-back-mark);
    text-transform: uppercase;
    line-height: 1.2;
  }
  .back__web {
    position: absolute;
    right: 34px; bottom: 26px;
    font-size: 14px;
    color: var(--back-text);
    letter-spacing: 0.5px;
  }
  /* Front */
  .card--front { left: 635px; background: var(--card-front); }
  .front__tab {
    position: absolute;
    right: 0; top: 34px;
    width: 14px; height: 52px;
    background: var(--gold);
  }
  .front__person {
    position: absolute;
    right: 28px; top: 30px;
    text-align: right;
  }
  .person__name {
    font-size: 30px;
    font-weight: 700;
    color: var(--gold-deep);
    line-height: 1.1;
  }
  .person__role {
    font-size: 14px;
    font-weight: 600;
    color: var(--ink);
    margin-top: 4px;
  }
  .front__brand {
    position: absolute;
    left: 32px; top: 34px;
    display: flex;
    align-items: center;
    gap: 10px;
  }
  .brand__square {
    width: 30px; height: 30px;
    background: var(--gold);
  }
  .brand__name {
    font-size: 13px;
    font-weight: 600;
    color: var(--silver);
    text-transform: uppercase;
    letter-spacing: 1.5px;
    line-height: 1.35;
  }
  .front__address {
    position: absolute;
    left: 32px; top: 124px;
    font-size: 15px;
    color: var(--ink);
    line-height: 1.45;
  }
  .front__contacts {
    position: absolute;
    left: 32px; bottom: 26px;
    list-style: none;
    font-size: 14px;
    color: var(--ink);
    line-height: 1.6;
  }
  .contact { display: flex; align-items: center; gap: 10px; }
  .contact svg { width: 13px; height: 13px; flex: none; }
</style>
</head>
<body>
  <section class="card card--back" aria-label="Card back">
    <div class="back__mark">Renwick Tolliver<br>Construction</div>
    <div class="back__web">www.renwick-tolliver.co.uk</div>
  </section>

  <section class="card card--front" aria-label="Card front">
    <div class="front__tab"></div>
    <div class="front__person">
      <div class="person__name">Lionel Ashby</div>
      <div class="person__role">Managing Director</div>
    </div>

    <div class="front__brand">
      <span class="brand__square"></span>
      <span class="brand__name">Renwick Tolliver<br>Construction</span>
    </div>

    <address class="front__address" style="font-style:normal">
      Halden Road, Westcombe<br>
      Ashbury, AB4 2QN
    </address>

    <ul class="front__contacts">
      <li class="contact">
        <svg viewBox="0 0 24 24" aria-hidden="true"><path fill="#e3a71f" d="M6.6 10.8a15.1 15.1 0 0 0 6.6 6.6l2.2-2.2c.3-.3.7-.4 1-.2 1.1.4 2.3.6 3.6.6.6 0 1 .4 1 1V20c0 .6-.4 1-1 1A17 17 0 0 1 3 4c0-.6.4-1 1-1h3.5c.6 0 1 .4 1 1 0 1.3.2 2.5.6 3.6.1.3 0 .7-.2 1z"/></svg>
        07822254961
      </li>
      <li class="contact">
        <svg viewBox="0 0 24 24" aria-hidden="true"><rect x="2" y="5" width="20" height="14" rx="2" fill="none" stroke="#e3a71f" stroke-width="2.2"/><path d="M3 6l9 7 9-7" fill="none" stroke="#e3a71f" stroke-width="2.2"/></svg>
        info@renwick-tolliver.co.uk
      </li>
      <li class="contact">
        <svg viewBox="0 0 24 24" aria-hidden="true"><circle cx="12" cy="12" r="9.5" fill="none" stroke="#e3a71f" stroke-width="2.2"/><path d="M2.5 12h19M12 2.5c3 3 3 16 0 19M12 2.5c-3 3-3 16 0 19" fill="none" stroke="#e3a71f" stroke-width="1.8"/></svg>
        www.renwick-tolliver.co.uk
      </li>
    </ul>
  </section>
</body>
</html>
```